Consulting company business cards

We have a base design, but would be willing to update. We have a new logo/"tag" that needs to be added. Current business card design is attached for reference into our "style."

Industry/Entity Type

Business

Contact Information for Business Card

Should contain name and title, office number, mobile number if appropriate, e-mail, website, physical address, and company logo.

Font styles to use
Other font styles liked:
• See current card design on KorvandBCard

Colors
0455a3
85acd3
aaaaaa

Requirements
Must have
• Our colors are navy blue, gray, and a lighter blue
Nice to have
• Design that I can easily drop in new names/titles as we hire employees.

```html
<!DOCTYPE html>
<html lang="en">
<head>
<meta charset="utf-8">
<title>Tavren business cards</title>
<link rel="stylesheet" href="https://fonts.googleapis.com/css2?family=Open+Sans:wdth,wght@75..100,400..700&display=swap">
<style>
  :root {
    --stage: #141414;
    --navy: #0b2f4e;
    --navy-ink: #0e3556;
    --light-blue: #a9c8e0;
    --rule-gray: #9ea4ab;
    --white: #ffffff;
    --text-font: "Open Sans", Arial, sans-serif;
  }
  * { margin: 0; padding: 0; box-sizing: border-box; }
  html, body { width: 1200px; height: 900px; overflow: hidden; }
  body { background: var(--stage); font-family: var(--text-font); position: relative; }

  .card {
    position: absolute;
    top: 306px;
    width: 440px;
    height: 271px;
    border-radius: 12px;
    overflow: hidden;
  }
  .card--front { left: 149px; background: var(--navy); color: var(--white); }
  .card--back { left: 608px; background: var(--white); color: var(--navy-ink); }

  .brand { position: absolute; }
  .brand__row { display: flex; align-items: center; gap: 8px; }
  .brand__name {
    font-weight: 700;
    font-stretch: 75%;
    line-height: 1;
    letter-spacing: 1px;
  }
  .brand__dot { border-radius: 50%; flex: none; }
  .brand__tag {
    font-size: 10.5px;
    letter-spacing: 1.4px;
    text-transform: uppercase;
    margin-top: 3px;
  }

  .card--front .brand { left: 206px; top: 44px; }
  .card--front .brand__name { font-size: 50px; color: var(--white); }
  .card--front .brand__dot { width: 36px; height: 36px; background: var(--white); }

  .card--back .brand { left: 104px; top: 100px; }
  .card--back .brand__name { font-size: 56px; color: var(--navy-ink); }
  .card--back .brand__dot { width: 40px; height: 40px; background: var(--light-blue); }
  .card--back .brand__tag { font-size: 11.5px; color: var(--navy-ink); }

  .person { position: absolute; left: 26px; top: 101px; }
  .person__name { font-size: 15px; font-weight: 700; line-height: 19px; }
  .person__title { font-size: 12.5px; line-height: 17px; }

  .divider {
    position: absolute; left: 0; right: 0; top: 149px;
    height: 2px; background: var(--rule-gray);
  }

  .contact {
    position: absolute; right: 30px; top: 176px;
    list-style: none; text-align: right;
    font-size: 12.5px; line-height: 16px;
  }
  .contact li { display: flex; justify-content: flex-end; align-items: center; gap: 6px; }
  .contact svg { width: 9px; height: 9px; fill: var(--white); flex: none; }
  .contact__address { margin-top: 6px; padding-right: 0; }
</style>
</head>
<body>
  <section class="card card--front" aria-label="Card front">
    <div class="brand">
      <div class="brand__row">
        <span class="brand__name">TAVREN</span>
        <span class="brand__dot"></span>
      </div>
      <div class="brand__tag">A Cloud Consulting Company</div>
    </div>

    <div class="person">
      <div class="person__name">Dana Korvand</div>
      <div class="person__title">Managing Director</div>
    </div>

    <div class="divider"></div>

    <ul class="contact">
      <li>555.014.2910
        <svg viewBox="0 0 10 10" aria-label="office phone"><path d="M1 4 C1 2 3 1 5 1 C7 1 9 2 9 4 L7 4.5 L6.5 3.5 L3.5 3.5 L3 4.5 Z M2.5 5.5 L7.5 5.5 L8.5 9 L1.5 9 Z"/></svg>
      </li>
      <li>555.014.2971
        <svg viewBox="0 0 10 10" aria-label="mobile phone"><path d="M2.5 0.5 H7.5 V9.5 H2.5 Z M3.5 2 V6.5 H6.5 V2 Z"/></svg>
      </li>
      <li>dkorvand@tavrentech.com
        <svg viewBox="0 0 10 10" aria-label="email"><path d="M0.5 2 H9.5 V8.5 H0.5 Z M1.2 2.6 L5 5.5 L8.8 2.6 Z" fill-rule="evenodd"/></svg>
      </li>
      <li class="contact__address">2197 N 48 th fairmont ohio 40512</li>
    </ul>
  </section>

  <section class="card card--back" aria-label="Card back">
    <div class="brand">
      <div class="brand__row">
        <span class="brand__name">TAVREN</span>
        <span class="brand__dot"></span>
      </div>
      <div class="brand__tag">A Cloud Consulting Company</div>
    </div>
  </section>
</body>
</html>
```